uk based ecommerce website requires fresh look ,high quality look and feel

we are a web based company selling eco friendly ground reinforcement grids to diy and construction sectors
our existing website is www.pondermeshpaths.co.uk ,

we have already updated the logo so that is the branding sorted .so we need a ecommerce website that is very much up-to date in design and layout and which has content management system for ease of use so that we can add products and information as required.

Use current logo as reference for colour scheme.
www.pondermeshpaths.co.uk

The current website has 6 pages accessible through the navigation bar, I would now like 5 pages, removing the need for the Trade Enquiries page possibly have it with along with contact us.

Target Market(s)

construction industry , diy end users,
retail market, landscapers, gardeners

Industry/Entity Type

Construction

Font styles to use
Other font styles liked:
• logo font prometo

Colors
f78f20
9bcb3c

Requirements
Must have
• logo colours and logo design in website with cms responsive design for tablet and mobile devices
• expect content to work flawlessly and look great across all devices
• HTML 5 custom design with coding as required
• must have good experiance in ecommerce website design
• eye catching, high quality look and feel and very user friedly ,very up-to date.
Nice to have
• picture slider show
• explain in writing what exactly i am getting in my ecommerce website
Should not have
• plain , basic design , old fashion looking ,cheap look

```html
<!DOCTYPE html>
<html lang="en">
<head>
<meta charset="utf-8">
<title>Pondermesh Ground Solutions</title>
<link href="https://fonts.googleapis.com/css2?family=Raleway:wght@300;400;500;600&display=swap" rel="stylesheet">
<style>
:root{
  --orange:#f78f20;
  --green:#9bcb3c;
  --green-dark:#85b52c;
  --text:#444;
  --muted:#888;
  --line:#e6e6e6;
  --footer:#3b3b3b;
  --footer-base:#303030;
  --white:#fff;
}
*{box-sizing:border-box;margin:0;padding:0}
html,body{width:675px;height:1200px;overflow:hidden}
body{font-family:'Raleway',sans-serif;color:var(--text);background:var(--white);position:relative}
a{color:inherit;text-decoration:none}
.abs{position:absolute}

/* header */
.site-header{position:absolute;left:0;top:0;width:675px;height:62px;border-top:2px solid var(--green);background:var(--white)}
.brand{position:absolute;display:flex;align-items:center;gap:6px}
.brand-mark{width:14px;height:14px;background:var(--green)}
.brand-name{font-weight:600;color:var(--orange);letter-spacing:.5px}
.site-header .brand{left:55px;top:20px}
.site-header .brand-name{font-size:15px}
.main-nav{position:absolute;top:27px;left:0;font-size:7.5px;color:#333}
.main-nav a{position:absolute;white-space:nowrap}
.nav-icon{position:absolute;top:22px;width:18px;height:18px;border-radius:50%;border:1px solid #eee;display:flex;align-items:center;justify-content:center}

/* hero */
.hero{position:absolute;left:0;top:62px;width:675px;height:264px;
  background:linear-gradient(180deg,#8a9a6a 0%,#b9b9b6 8%,#9a9a98 40%,#6e6e6e 60%,#b5b5b2 85%,#cfcfcc 100%);
  clip-path:polygon(0 0,100% 0,100% 94%,50% 100%,0 94%)}
.hero-box{position:absolute;left:165px;top:60px;width:338px;height:131px;background:rgba(0,0,0,.55);outline:1px solid rgba(255,255,255,.6);outline-offset:-5px;text-align:center;color:var(--white)}
.hero-title{font-size:25px;font-weight:500;margin-top:17px}
.hero-sub{font-size:20px;font-weight:300;margin-top:4px}
.hero-actions{display:flex;justify-content:center;gap:18px;margin-top:11px}
.hero-btn{width:89px;height:26px;border:1px solid rgba(255,255,255,.7);font-size:12px;font-weight:500;display:flex;align-items:center;justify-content:center}
.slide-arrow{position:absolute;width:10px;height:14px}

/* sections */
.section-title{position:absolute;left:55px;display:flex;align-items:center;gap:7px;font-size:15px;font-weight:500;color:var(--orange)}
.section-title .dot{width:9px;height:14px;background:var(--green)}
.section-title .sub{color:var(--muted);font-size:10px;font-weight:400;margin-left:4px}
.section-title .slash{color:var(--orange);font-size:15px;margin-left:4px}
.intro{position:absolute;left:55px;top:372px;width:500px;font-size:6.6px;line-height:14.5px;color:#555}
.intro-hint{position:absolute;left:55px;top:412px;font-size:7px;color:var(--green)}

.card{position:absolute;width:136px;border:1px solid var(--line);background:var(--white);text-align:center}
.card .photo{position:absolute;left:5px;top:5px;width:126px;height:99px}
.cat-card{top:437px;height:138px}
.cat-card .label{position:absolute;left:0;right:0;top:117px;font-size:7px;color:#444}
.divider{position:absolute;left:55px;top:600px;width:565px;height:1px;background:var(--green)}
.product-card{top:655px;height:162px}
.product-card .name{position:absolute;left:0;right:0;top:111px;font-size:11.5px;color:#333}
.product-card .price{position:absolute;left:0;right:0;top:129px;font-size:8px;color:#666}
.product-card .option{position:absolute;left:0;right:0;top:142px;font-size:8.5px;color:var(--green);text-decoration:underline}

/* gallery */
.gallery{position:absolute;left:0;top:844px;width:675px;height:176px;background:linear-gradient(135deg,#a3d045,#8fc03a)}
.gallery .section-title{color:var(--white);top:22px}
.gallery-item{position:absolute;top:66px;width:135px;height:81px;border:2px solid rgba(255,255,255,.85)}
.gallery-item .overlay{position:absolute;inset:0;background:rgba(255,255,255,.35);display:flex;align-items:center;justify-content:center;font-size:9.5px;color:#222}

/* footer */
.site-footer{position:absolute;left:0;top:1020px;width:675px;height:140px;background:var(--footer);color:#ddd}
.site-footer .brand{left:55px;top:60px}
.site-footer .brand-name{font-size:14px}
.foot-col{position:absolute;top:26px;font-size:6.4px}
.foot-col h4{font-size:8.5px;font-weight:500;color:var(--white);margin-bottom:8px}
.foot-col li{list-style:none;height:15.5px}
.foot-col li::before{content:"»";margin-right:7px}
.contact-row{display:flex;gap:8px;line-height:12.5px;margin-bottom:8px}
.contact-row svg{flex:none;margin-top:1px}
.social{display:flex;gap:7px;margin-top:4px}
.social span{width:20px;height:20px;border:1.5px solid #eee;border-radius:50%}
.base-bar{position:absolute;left:0;top:1160px;width:675px;height:40px;background:var(--footer-base);color:#ddd;font-size:6.8px;display:flex;align-items:center;justify-content:center;gap:5px}
</style>
</head>
<body>

<header class="site-header">
  <a class="brand" href="#"><span class="brand-mark"></span><span class="brand-name">PONDERMESH</span></a>
  <nav class="main-nav">
    <a style="left:243px" href="#">Shop</a>
    <a style="left:296px" href="#">About Us</a>
    <a style="left:363px" href="#">Ground solutions</a>
    <a style="left:454px" href="#">Ponder Mesh</a>
    <a style="left:525px" href="#">Contact Us</a>
  </nav>
  <span class="nav-icon" style="left:578px" aria-label="Search">
    <svg width="8" height="8" viewBox="0 0 10 10"><circle cx="4" cy="4" r="3" fill="none" stroke="#9bcb3c" stroke-width="1.6"/><line x1="6.3" y1="6.3" x2="9" y2="9" stroke="#9bcb3c" stroke-width="1.8"/></svg>
  </span>
  <span class="nav-icon" style="left:603px" aria-label="Basket">
    <svg width="8" height="8" viewBox="0 0 10 10"><path d="M0 1h2l1 5h6l1-4H3" fill="none" stroke="#9bcb3c" stroke-width="1.4"/><circle cx="4" cy="8.5" r="1" fill="#9bcb3c"/><circle cx="8" cy="8.5" r="1" fill="#9bcb3c"/></svg>
  </span>
</header>

<section class="hero" role="img" aria-label="Gravel-filled cellular paving grid close up">
  <div class="hero-box">
    <h1 class="hero-title">Ponder Mesh System</h1>
    <p class="hero-sub">24 Hour Messaging Service</p>
    <div class="hero-actions"><a class="hero-btn" href="#">Log in</a><a class="hero-btn" href="#">Register</a></div>
  </div>
  <svg class="slide-arrow" style="left:26px;top:122px" viewBox="0 0 10 14"><path d="M8 1L2 7l6 6" fill="none" stroke="#fff" stroke-width="1.8"/></svg>
  <svg class="slide-arrow" style="left:634px;top:126px" viewBox="0 0 10 14"><path d="M2 1l6 6-6 6" fill="none" stroke="#fff" stroke-width="1.8"/></svg>
</section>

<h2 class="section-title" style="top:340px"><span class="dot"></span>Pondermesh Eco Solutions Ltd</h2>
<p class="intro">Stabilised Gravel Paving grids combines purpose designed Cellular reinforcement Pavers with the natural appearance, strength, security and free draining characteristics of a loose aggregate surface</p>
<p class="intro-hint">Please Select Category Below</p>

<svg class="slide-arrow" style="left:29px;top:498px" viewBox="0 0 10 14"><path d="M8 1L2 7l6 6" fill="none" stroke="#999" stroke-width="1.4"/></svg>
<svg class="slide-arrow" style="left:631px;top:498px" viewBox="0 0 10 14"><path d="M2 1l6 6-6 6" fill="none" stroke="#999" stroke-width="1.4"/></svg>

<div class="card cat-card" style="left:55px"><div class="photo" role="img" aria-label="Geotextile membrane laid on a site beside a fence" style="background:linear-gradient(180deg,#a9b7c2 0%,#8b7f62 35%,#3a3a3a 60%,#555 100%)"></div><span class="label">Geotextile Membranes (2)</span></div>
<div class="card cat-card" style="left:198px"><div class="photo" role="img" aria-label="Gravel over black cellular grid for light driveways" style="background:linear-gradient(180deg,#1f4a2a 0%,#bdbdbd 15%,#9a9a9a 55%,#2b2b2b 100%)"></div><span class="label">Light Domestic Driveways (2)</span></div>
<div class="card cat-card" style="left:341px"><div class="photo" role="img" aria-label="Green grass growing through a heavy-duty grid" style="background:linear-gradient(135deg,#6c8c4a,#4d6a3a 50%,#7f9a5c)"></div><span class="label">Heavy Domestic Driveways (4)</span></div>
<div class="card cat-card" style="left:484px"><div class="photo" role="img" aria-label="Planted raised bed beside a parking surface" style="background:linear-gradient(180deg,#6f8a4c 0%,#c9a06b 45%,#d8b384 75%,#58783a 100%)"></div><span class="label">Commercial Parking System (1)</span></div>

<div class="divider"></div>

<h2 class="section-title" style="top:618px"><span class="dot"></span>Featured Products<span class="slash">/</span><span class="sub">All Products</span></h2>

<div class="card product-card" style="left:55px"><div class="photo" role="img" aria-label="Silver car parked on a gravel drive" style="background:linear-gradient(180deg,#5c7a4a 0%,#a9a9a9 45%,#8d8d8d 70%,#6f6f6f 100%)"></div><span class="name">Debet Efficiantur</span><span class="price">£ 11.00 each</span><a class="option" href="#">Option</a></div>
<div class="card product-card" style="left:198px"><div class="photo" role="img" aria-label="Bicycle wheel on gravel-filled grid" style="background:linear-gradient(180deg,#4a4a4a,#8f8f8f 50%,#6a6a6a)"></div><span class="name">Minim Vivendum</span><span class="price">£ 9.58 each</span><a class="option" href="#">Option</a></div>
<div class="card product-card" style="left:341px"><div class="photo" role="img" aria-label="Lorry wheels driving over a black paving grid" style="background:linear-gradient(180deg,#8c8c88,#4e4e4c 50%,#a8a49c)"></div><span class="name">Dicit Euismod</span><span class="price">£ 11.00 each</span><a class="option" href="#">Option</a></div>
<div class="card product-card" style="left:484px"><div class="photo" role="img" aria-label="Truck wheel resting on a stabilised gravel surface" style="background:linear-gradient(135deg,#cfc6b4,#b3aa98 45%,#3d3d3d 80%)"></div><span class="name">Debet Efficiantur</span><span class="price">£ 9.58 each</span><a class="option" href="#">Option</a></div>

<section class="gallery">
  <h2 class="section-title"><span class="dot" style="background:var(--orange)"></span>Photo Gallery</h2>
  <svg class="slide-arrow" style="left:26px;top:100px" viewBox="0 0 10 14"><path d="M8 1L2 7l6 6" fill="none" stroke="#fff" stroke-width="1.8"/></svg>
  <svg class="slide-arrow" style="left:637px;top:100px" viewBox="0 0 10 14"><path d="M2 1l6 6-6 6" fill="none" stroke="#fff" stroke-width="1.8"/></svg>
  <div class="gallery-item" style="left:55px" role="img" aria-label="Bicycle wheel on gravel grid" ><div style="position:absolute;inset:0;background:linear-gradient(135deg,#b5b5b5,#7c7c7c)"></div><div class="overlay">View Details &gt;&gt;</div></div>
  <div class="gallery-item" style="left:199px;background:linear-gradient(180deg,#c9d3dc 0%,#e8e8e6 45%,#8a6a48 75%,#b08a5a 100%)" role="img" aria-label="House with a finished gravel driveway"></div>
  <div class="gallery-item" style="left:342px;background:linear-gradient(135deg,#7d8f5a,#9a5a48 45%,#a36a55 80%,#6a8a4a)" role="img" aria-label="Garden path with paving edge"></div>
  <div class="gallery-item" style="left:485px;background:linear-gradient(180deg,#6f8a55 0%,#c79a5a 35%,#1f2a4a 70%,#2a3050 100%)" role="img" aria-label="Tractor spreading gravel onto a laid grid"></div>
</section>

<footer class="site-footer">
  <a class="brand" href="#"><span class="brand-mark"></span><span class="brand-name">PONDERMESH</span></a>
  <div class="foot-col" style="left:198px">
    <h4>MENUS</h4>
    <ul><li>Shop</li><li>About Us</li><li>Ground solutions</li><li>Ponder Mesh</li><li>Contact Us</li></ul>
  </div>
  <div class="foot-col" style="left:291px">
    <h4>QUICK LINKS</h4>
    <ul><li>Site map</li><li>Terms and Conditions</li><li>Disclaimer</li><li>Privacy Policy</li><li>Contact us</li></ul>
  </div>
  <div class="foot-col" style="left:396px;width:130px">
    <h4>CONTACT US</h4>
    <div class="contact-row"><svg width="10" height="9" viewBox="0 0 10 9"><path d="M5 0L0 4.5h1.5V9h2.5V6h2v3h2.5V4.5H10z" fill="#eee"/></svg><span>Harlow Mill House,<br>Brookside Trade Park,<br>Fenwick, FK9 4QT</span></div>
    <div class="contact-row"><svg width="10" height="10" viewBox="0 0 10 10"><rect x="2.5" y="0.5" width="5" height="9" rx="1" fill="none" stroke="#eee"/></svg><span>0140-555-0182 , 0845-555-0145</span></div>
    <div class="contact-row"><svg width="10" height="10" viewBox="0 0 10 10"><rect x="0.5" y="2" width="9" height="6.5" fill="none" stroke="#eee"/><path d="M0.5 2l4.5 3.5L9.5 2" fill="none" stroke="#eee"/></svg><span>info@pondermesh.example</span></div>
  </div>
  <div class="foot-col" style="left:519px">
    <h4>CONNECT US WITH</h4>
    <div class="social"><span aria-label="Social profile 1"></span><span aria-label="Social profile 2"></span><span aria-label="News feed"></span><span aria-label="Social profile 3"></span></div>
  </div>
</footer>

<div class="base-bar">
  <svg width="8" height="8" viewBox="0 0 10 10"><circle cx="5" cy="5" r="4.3" fill="none" stroke="#ddd"/><path d="M6.6 3.6A2 2 0 1 0 6.6 6.4" fill="none" stroke="#ddd"/></svg>
  <span>Companyname 2016 . All Rights Reserved</span>
</div>

</body>
</html>
```